Adelaide based cleaning and remediation business needs a website design

We are launching a new company with no clients as yet so we don't have the benefit of Plimora Reviews to build confidence. We can use our  past work history with other employers in the industry to give some credibility. Happy to use any colour scheme as long as it look interesting when people click on the site it gets there attention. enquiry . I have supplied a mock up the important information and various photos as they tell a lot of the story.

```html
<!DOCTYPE html>
<html lang="en">
<head>
<meta charset="utf-8">
<title>Kestrel Services – Dirty Job Cleaners Adelaide</title>
<link rel="stylesheet" href="https://fonts.googleapis.com/css2?family=Bebas+Neue&family=Roboto:wght@400;500;700&display=swap">
<style>
:root{
  --deep:#1b5842;
  --deep-dark:#134733;
  --ink:#0f4634;
  --green:#39a548;
  --green-soft:#e9f5ea;
  --grey-bg:#f2f4f3;
  --text:#4b4b4b;
  --muted:#7b7b7b;
  --white:#ffffff;
  --star:#f5a623;
}
*{box-sizing:border-box;margin:0;padding:0}
html,body{width:1200px;height:4162px;overflow:hidden}
body{position:relative;font-family:"Roboto",Arial,sans-serif;color:var(--text);background:var(--white)}
.abs{position:absolute}
.display{font-family:"Bebas Neue","Oswald",sans-serif;font-weight:400;color:var(--ink);letter-spacing:.5px;line-height:1.05}
.eyebrow{font-size:15px;font-weight:500;color:var(--green);letter-spacing:.5px;text-transform:uppercase}
.btn{display:inline-flex;align-items:center;justify-content:center;gap:8px;border-radius:30px;font-weight:700;font-size:15px;text-transform:uppercase;white-space:nowrap}
.btn-green{background:var(--green);color:var(--white)}
.photo{display:block}

/* header */
.header{left:0;top:0;width:1200px;height:121px;background:var(--white)}
.logo{left:113px;top:-60px;width:178px;height:242px;border-radius:0 0 90px 90px;background:var(--white);z-index:5;display:flex;align-items:flex-end;justify-content:center;padding-bottom:36px;flex-direction:column;text-align:center}
.logo-name{font-weight:700;font-size:18px;color:var(--ink);display:flex;align-items:center;gap:8px;justify-content:center;width:100%}
.logo-name i{width:14px;height:14px;background:var(--green);display:inline-block;border-radius:50%}
.contact-top{top:18px;display:flex;align-items:center;gap:14px;white-space:nowrap}
.contact-top small{display:block;font-size:13px;color:#333}
.contact-top b{font-size:16px;color:#111;font-weight:500}
.contact-top b.big{font-size:22px;font-weight:700}
.divider-v{left:868px;top:14px;width:1px;height:52px;background:#ddd}
.navbar{left:290px;top:81px;width:910px;height:36px;background:var(--green)}
.navbar ul{list-style:none;display:flex;height:100%;align-items:center;padding-left:30px}
.navbar li{color:var(--white);font-weight:700;font-size:15px;padding:0 13px;height:100%;display:flex;align-items:center}
.navbar li.active{background:var(--deep)}
.quote-nav{left:900px;top:81px;width:300px;height:36px;background:var(--green);color:var(--white);font-weight:700;font-size:15px;display:flex;align-items:center;padding-left:48px}
.quote-nav:before{content:"";position:absolute;left:0;top:0;width:22px;height:36px;background:var(--white);transform:skewX(-30deg);transform-origin:top left}

/* hero */
.hero{left:0;top:121px;width:1200px;height:502px;background:var(--deep);overflow:hidden}
.hero-copy{left:110px;top:130px;width:480px;color:var(--white)}
.hero-copy h1{font-size:52px;color:var(--white);margin-top:8px}
.hero-copy p{font-size:16px;line-height:1.55;margin-top:18px;font-weight:500}
.hero-actions{display:flex;gap:14px;margin-top:22px}
.hero-actions .btn{height:48px;padding:0 34px;text-transform:none;font-size:16px}
.btn-white{background:var(--white);color:var(--ink)}

/* services */
.services{left:0;top:622px;width:1200px;height:770px;background:var(--grey-bg);text-align:center}
.services .eyebrow{position:absolute;left:0;width:100%;top:86px;font-size:14px}
.services h2{position:absolute;left:0;width:100%;top:108px;font-size:42px}
.card{top:190px;width:315px;height:394px;background:var(--white);border-radius:8px;box-shadow:0 6px 22px rgba(0,0,0,.08);overflow:hidden}
.card .photo{width:100%;height:217px}
.card-icon{position:absolute;left:126px;top:185px;width:64px;height:64px;border-radius:50%;background:var(--white);box-shadow:0 3px 10px rgba(0,0,0,.12);display:flex;align-items:center;justify-content:center}
.card h3{margin-top:52px;font-size:19px;font-weight:700;color:#111}
.card p{margin:12px 22px 0;font-size:13px;line-height:1.6;color:var(--muted)}
.card .more{margin-top:14px;font-size:13px;font-weight:700;color:var(--green);letter-spacing:.5px}
.services .btn{position:absolute;left:480px;top:633px;width:240px;height:53px}

/* about */
.about-photo{left:111px;top:1491px;width:529px;height:440px}
.help-box{left:145px;top:1902px;width:443px;height:123px;background:var(--white);box-shadow:0 6px 20px rgba(0,0,0,.08);padding:22px 36px}
.help-box h4{font-size:18px;font-weight:400;color:#111}
.help-box h4 b{font-weight:700}
.help-row{display:flex;align-items:center;gap:20px;margin-top:14px}
.help-row .btn{height:34px;padding:0 18px;font-size:13px}
.call-mini{display:flex;align-items:center;gap:10px;white-space:nowrap}
.call-mini small{display:block;font-size:11px;color:#555}
.call-mini b{font-size:16px;color:#111;font-weight:500;letter-spacing:.5px}
.about-copy{left:719px;top:1509px;width:380px}
.about-copy h2{font-size:43px;margin-top:14px}
.about-copy p{font-size:14px;line-height:1.75;color:var(--muted);margin-top:26px}
.about-copy p + p{margin-top:20px}
.about-copy .btn{margin-top:30px;height:44px;padding:0 24px;font-size:14px}

/* testimonials */
.testimonials{left:0;top:2132px;width:1200px;height:486px;background:var(--green);text-align:center}
.testimonials .eyebrow{position:absolute;left:0;width:100%;top:64px;color:var(--white);font-size:17px}
.testimonials h2{position:absolute;left:0;width:100%;top:92px;font-size:42px;color:var(--white)}
.t-card{top:189px;width:407px;height:231px;background:var(--white);border-radius:30px;text-align:left;padding:22px 22px 0 88px}
.quote-mark{font-family:Georgia,serif;font-size:66px;line-height:.8;color:var(--deep);font-weight:700}
.t-card p{font-size:13.5px;line-height:1.75;color:var(--muted);margin-top:6px}
.t-card h5{font-size:17px;font-weight:500;color:#111;margin-top:10px}
.stars{color:var(--star);font-size:16px;letter-spacing:2px}
.avatar{width:114px;height:114px;border-radius:50%;border:4px solid var(--white)}

/* faq */
.faq-copy{left:111px;top:2735px;width:440px}
.faq-copy h2{font-size:43px;margin-top:14px}
.faq-item{left:111px;width:429px;height:52px;border-radius:26px;background:var(--white);box-shadow:0 3px 10px rgba(0,0,0,.12);display:flex;align-items:center;justify-content:space-between;padding:0 22px;font-weight:500;font-size:15px;color:#111}
.faq-photo{left:607px;top:2713px;width:482px;height:480px}

/* estimate */
.estimate{left:0;top:3295px;width:1200px;height:460px;background:var(--deep);overflow:hidden}
.estimate-copy{left:722px;top:42px;width:380px;color:var(--white)}
.estimate-copy .eyebrow{font-size:15px}
.estimate-copy h2{font-size:40px;color:var(--white);margin-top:6px}
.estimate-copy p{font-size:14px;line-height:1.5;margin-top:8px}
.field{height:34px;border-radius:17px;background:rgba(255,255,255,.1);border:1px solid rgba(255,255,255,.15);font-size:11px;color:var(--white);padding:0 15px;display:flex;align-items:center}
.form-grid{left:722px;top:180px;width:366px;display:grid;grid-template-columns:1fr 1fr;gap:10px 12px}
.form-grid .msg{grid-column:span 2;height:82px;align-items:flex-start;padding-top:14px;border-radius:14px}
.form-foot{left:722px;top:391px;display:flex;align-items:center;gap:22px;color:var(--white)}
.form-foot .btn{height:38px;padding:0 20px;font-size:14px}
.form-foot small{display:block;font-size:11px;color:var(--white)}
.form-foot b{font-size:13px;color:var(--green);font-weight:500;text-decoration:underline}

/* footer */
.footer{left:0;top:3755px;width:1200px;height:407px;background:var(--white)}
.badge{left:111px;top:80px;width:240px;height:92px;display:flex;align-items:center;gap:18px}
.badge .seal{width:90px;height:90px;border-radius:50%;background:var(--green-soft);border:6px solid #9fcf6a}
.badge .plate{width:132px;height:34px;background:#e6e9ee;border-radius:4px}
.socials{left:186px;top:212px;display:flex;gap:18px}
.socials span{width:11px;height:11px;border-radius:50%;background:#555}
.f-col h6{font-size:16px;font-weight:700;color:#222}
.f-col{top:76px}
.f-item{display:flex;gap:12px;margin-top:18px;font-size:13px;color:#555;line-height:1.4}
.f-item b{display:block;font-size:11px;color:#111}
.f-links{list-style:none;margin-top:16px;font-size:13px;color:#666;line-height:2}
.f-col p{font-size:12px;color:#666;line-height:1.6;margin-top:16px}
.f-col .btn{margin-top:20px;width:200px;height:42px;border-radius:4px;font-size:15px}
.foot-line{left:111px;top:4082px;width:978px;height:1px;background:#ddd}
.go-up{left:1006px;top:4065px;width:82px;height:22px;background:#eee;border-radius:12px;font-size:11px;font-weight:700;color:#111;display:flex;align-items:center;justify-content:center}
.copyright{left:111px;top:4120px;font-size:13px;color:#555}
.legal{left:760px;top:4120px;font-size:13px;color:#555;word-spacing:2px}
</style>
</head>
<body>

<header class="abs header">
  <div class="abs logo"><div class="logo-name"><i></i>Kestrel</div></div>
  <div class="abs contact-top" style="left:590px">
    <svg width="36" height="28" viewBox="0 0 36 28"><rect x="1.5" y="1.5" width="33" height="25" fill="none" stroke="var(--green)" stroke-width="2.5"/><path d="M2 3l16 13L34 3" fill="none" stroke="var(--green)" stroke-width="2.5"/></svg>
    <div><small>Email Us</small><b>admin@kestrelsvc.com</b></div>
  </div>
  <div class="abs divider-v"></div>
  <div class="abs contact-top" style="left:898px">
    <svg width="38" height="38" viewBox="0 0 38 38"><circle cx="19" cy="19" r="17" fill="none" stroke="var(--green)" stroke-width="2.5"/><path d="M12 11c1-1 3-1 4 1l1 3c0 1-1 2-2 2 1 3 3 5 6 6 0-1 1-2 2-2l3 1c2 1 2 3 1 4-2 2-5 2-9-1-4-3-7-7-7-10 0-2 0-3 1-4z" fill="var(--green)"/></svg>
    <div><small>Call Us Today!</small><b class="big">0400 555 019</b></div>
  </div>
  <nav class="abs navbar"><ul>
    <li class="active">HOME</li><li>ABOUT US</li><li>OUR SERVICES</li><li>FAQS</li><li>PRICING</li><li>CONTACT US</li>
  </ul></nav>
  <div class="abs quote-nav">REQUEST A QUOTE</div>
</header>

<section class="abs hero">
  <svg class="abs" style="left:0;top:0" width="1200" height="502" viewBox="0 0 1200 502">
    <defs><linearGradient id="heroPhoto" x1="0" y1="0" x2="1" y2="1"><stop offset="0" stop-color="#3d3a38"/><stop offset=".5" stop-color="#5a6070"/><stop offset="1" stop-color="#2f3a4a"/></linearGradient></defs>
    <path d="M800 0 C660 120 590 300 575 502 L1200 502 L1200 0 Z" fill="var(--green)"/>
    <path d="M822 0 C690 130 612 310 604 502 L1200 502 L1200 0 Z" fill="url(#heroPhoto)" role="img" aria-label="Cleaner in a blue protective suit and respirator clearing fire debris"/>
  </svg>
  <div class="abs hero-copy">
    <div class="eyebrow" style="font-size:17px">Experts Who Care</div>
    <h1 class="display">We do the dirty jobs<br>no one else wants to.</h1>
    <p>Specialised Clean-Ups for Squalor, Fire, and Pigeon<br>Waste in Adelaide.</p>
    <div class="hero-actions"><span class="btn btn-green">Dirty Job Cleaners</span><span class="btn btn-white">Get a Quote</span></div>
  </div>
</section>

<section class="abs services">
  <div class="eyebrow">What We Offers</div>
  <h2 class="display">Our Pest Control Services</h2>
  <article class="abs card" style="left:103px">
    <div class="photo" role="img" aria-label="Yard piled with rubbish and an old bicycle" style="background:linear-gradient(135deg,#6b5a4a,#3e3a36 60%,#8a7a66)"></div>
    <div class="card-icon"><svg width="30" height="30" viewBox="0 0 30 30"><rect x="5" y="6" width="20" height="20" fill="none" stroke="var(--green)" stroke-width="2.5"/><path d="M9 12h12M9 17h12M9 22h12" stroke="var(--green)" stroke-width="2"/></svg></div>
    <h3>End of lease &amp; estate Clean</h3>
    <p>Lorem ipsum consectetur adipiscing elit, sed labore et dolore magna aliqua.</p>
    <div class="more">LEARN MORE »</div>
  </article>
  <article class="abs card" style="left:443px">
    <div class="photo" role="img" aria-label="Worker in white protective suit cleaning pigeon waste in a roof space" style="background:linear-gradient(135deg,#3a3a36,#6d6a60 55%,#2a2a28)"></div>
    <div class="card-icon"><svg width="30" height="30" viewBox="0 0 30 30"><path d="M4 16c5-1 9 0 12 4 3-6 7-9 11-10-2 8-6 14-13 14-5 0-8-3-10-8z" fill="var(--green)"/></svg></div>
    <h3>Pigeon Waste Clean Ups</h3>
    <p>Lorem ipsum consectetur adipiscing elit, sed labore et dolore magna aliqua.</p>
    <div class="more">LEARN MORE »</div>
  </article>
  <article class="abs card" style="left:782px">
    <div class="photo" role="img" aria-label="Fire damaged shed interior with burnt shelving" style="background:linear-gradient(135deg,#5c5f66,#2e2f33 60%,#77767a)"></div>
    <div class="card-icon"><svg width="30" height="30" viewBox="0 0 30 30"><rect x="6" y="10" width="18" height="16" fill="none" stroke="var(--green)" stroke-width="2.5"/><path d="M15 3c3 3 3 5 0 7-3-2-3-4 0-7z" fill="var(--green)"/></svg></div>
    <h3>Fire Damage Clean Outs</h3>
    <p>Lorem ipsum consectetur adipiscing elit, sed labore et dolore magna aliqua.</p>
    <div class="more">LEARN MORE »</div>
  </article>
  <span class="btn btn-green">Get a Quick Quote</span>
</section>

<div class="abs about-photo photo" role="img" aria-label="Roof cavity filled with bird droppings beside a cleaning brush" style="background:linear-gradient(135deg,#5b5a52,#8c8a7e 45%,#3a3b35)"></div>
<div class="abs help-box">
  <h4>Need Help? <b>Contact us Today!</b></h4>
  <div class="help-row">
    <span class="btn btn-green">Request Services ➜</span>
    <div class="call-mini">
      <svg width="34" height="34" viewBox="0 0 34 34"><circle cx="17" cy="17" r="17" fill="var(--deep)"/><path d="M11 10c1-1 2-1 3 1l1 3c0 1-1 1-2 2 1 2 3 4 5 5 1-1 1-2 2-2l3 1c2 1 2 2 1 3-2 2-5 1-8-1-3-3-6-6-6-9 0-2 0-2 1-3z" fill="#fff"/></svg>
      <div><small>Call Us Today</small><b>888-888-8888</b></div>
    </div>
  </div>
</div>
<div class="abs about-copy">
  <div class="eyebrow">About Us</div>
  <h2 class="display">The Best Pest Control<br>Experts Around</h2>
  <p>Adelaide-based Kestrel Services is a family-run organisation. We have been in operation for more than two decades. We've gained some knowledge about cleaning and squalor removal services throughout the years.</p>
  <p>As a small South Australian company, we base everything on responsibility honesty and fairness. We are aware of the confidence you put in us when you seek our help.</p>
  <span class="btn btn-green">Read More ➜</span>
</div>

<section class="abs testimonials">
  <div class="eyebrow">Testimonials</div>
  <h2 class="display">What Our Customer Says</h2>
  <div class="abs t-card" style="left:165px">
    <div class="quote-mark">“</div>
    <p>Marcus and his team arrived the next morning to clean up a rental property my husband and I own which and had been trashed by the</p>
    <h5>John Doe</h5><div class="stars">★★★★★</div>
  </div>
  <div class="abs avatar" style="left:111px;top:246px;background:linear-gradient(135deg,#4f86b5,#2a4e70)" role="img" aria-label="Customer portrait"></div>
  <div class="abs t-card" style="left:680px">
    <div class="quote-mark">“</div>
    <p>Engaged Kestrel Services to clean bird poo from our commercial building facade. Job was so well done it exceeded our expectations</p>
    <h5>John Doe</h5><div class="stars">★★★★★</div>
  </div>
  <div class="abs avatar" style="left:626px;top:246px;background:linear-gradient(135deg,#4f86b5,#2a4e70)" role="img" aria-label="Customer portrait"></div>
  <svg class="abs" style="left:40px;top:284px" width="24" height="36" viewBox="0 0 24 36"><path d="M20 3L5 18l15 15" fill="none" stroke="#fff" stroke-width="4"/></svg>
  <svg class="abs" style="left:1136px;top:284px" width="24" height="36" viewBox="0 0 24 36"><path d="M4 3l15 15L4 33" fill="none" stroke="#fff" stroke-width="4"/></svg>
</section>

<div class="abs faq-copy">
  <div class="eyebrow">FAQ</div>
  <h2 class="display">Frequently Asked<br>Questions</h2>
</div>
<div class="abs faq-item" style="top:2899px">About Us<svg width="20" height="20" viewBox="0 0 20 20"><circle cx="10" cy="10" r="10" fill="var(--green)"/><path d="M8 5l5 5-5 5" fill="none" stroke="#fff" stroke-width="2.4"/></svg></div>
<div class="abs faq-item" style="top:2970px">Pricing<svg width="20" height="20" viewBox="0 0 20 20"><circle cx="10" cy="10" r="10" fill="var(--green)"/><path d="M8 5l5 5-5 5" fill="none" stroke="#fff" stroke-width="2.4"/></svg></div>
<div class="abs faq-item" style="top:3041px">Qualifications<svg width="20" height="20" viewBox="0 0 20 20"><circle cx="10" cy="10" r="10" fill="var(--green)"/><path d="M8 5l5 5-5 5" fill="none" stroke="#fff" stroke-width="2.4"/></svg></div>
<div class="abs faq-item" style="top:3112px">We accept all major credit cards<svg width="20" height="20" viewBox="0 0 20 20"><circle cx="10" cy="10" r="10" fill="var(--green)"/><path d="M8 5l5 5-5 5" fill="none" stroke="#fff" stroke-width="2.4"/></svg></div>
<div class="abs faq-photo photo" role="img" aria-label="Fire damaged kitchen with burnt cabinets and exposed insulation" style="background:linear-gradient(160deg,#3b2d26,#6a4f40 40%,#1f1b19 75%,#5a4a40)"></div>

<section class="abs estimate">
  <svg class="abs" style="left:0;top:0" width="1200" height="460" viewBox="0 0 1200 460">
    <defs><linearGradient id="estPhoto" x1="0" y1="0" x2="1" y2="1"><stop offset="0" stop-color="#8a5a3a"/><stop offset=".45" stop-color="#c7b48a"/><stop offset="1" stop-color="#2e2a26"/></linearGradient></defs>
    <path d="M395 0 C520 110 610 280 665 460 L0 460 L0 0 Z" fill="var(--green)"/>
    <path d="M370 0 C490 115 575 285 625 460 L0 460 L0 0 Z" fill="url(#estPhoto)" role="img" aria-label="Worker in protective suit cleaning a bird-fouled gutter"/>
  </svg>
  <div class="abs estimate-copy">
    <div class="eyebrow">Request Callback</div>
    <h2 class="display">Get Your Free Estimaate</h2>
    <p>Complete the form below and we will contact you to discuss your pest problem!</p>
  </div>
  <div class="abs form-grid" style="top:180px">
    <div class="field">Name *</div><div class="field">Email Address*</div>
    <div class="field">Phone*</div><div class="field">Choose a service</div>
    <div class="field msg">Message</div>
  </div>
  <div class="abs form-foot" style="top:391px">
    <span class="btn btn-green">Submit ➜</span>
    <span style="font-size:11px">Or</span>
    <div class="call-mini">
      <svg width="34" height="34" viewBox="0 0 34 34"><circle cx="17" cy="17" r="16" fill="none" stroke="#fff" stroke-width="1.5"/><path d="M11 10c1-1 2-1 3 1l1 3c0 1-1 1-2 2 1 2 3 4 5 5 1-1 1-2 2-2l3 1c2 1 2 2 1 3-2 2-5 1-8-1-3-3-6-6-6-9 0-2 0-2 1-3z" fill="#fff"/></svg>
      <div><small>For Faster Service</small><b>(888) 888-8888</b></div>
    </div>
  </div>
</section>

<footer class="abs footer">
  <div class="abs badge" role="img" aria-label="Industry certification badge"><div class="seal"></div><div class="plate"></div></div>
  <div class="abs socials" aria-label="Social links"><span></span><span></span><span></span><span></span></div>
  <div class="abs f-col" style="left:420px;width:260px">
    <h6>Our Office Address</h6>
    <div class="f-item"><svg width="14" height="14" viewBox="0 0 14 14"><path d="M3 1c1 0 2 2 2 3s-1 1-1 2c1 2 2 3 4 4 1 0 1-1 2-1s3 1 3 2-1 2-3 2C6 13 1 8 1 4c0-2 1-3 2-3z" fill="var(--green)"/></svg><div><b>Phone</b>0400 555 019</div></div>
    <div class="f-item"><svg width="14" height="12" viewBox="0 0 14 12"><rect width="14" height="12" fill="var(--green)"/><path d="M0 1l7 5 7-5" fill="none" stroke="#fff" stroke-width="1.4"/></svg><div><b>Email</b>admin@kestrelsvc.com</div></div>
    <div class="f-item"><svg width="12" height="16" viewBox="0 0 12 16"><path d="M6 0a6 6 0 0 1 6 6c0 4-6 10-6 10S0 10 0 6a6 6 0 0 1 6-6z" fill="var(--green)"/><circle cx="6" cy="6" r="2" fill="#fff"/></svg><div><b>Address</b>12 Halden Street Norwood SA 5067</div></div>
    <div class="f-item"><svg width="12" height="16" viewBox="0 0 12 16"><path d="M6 0a6 6 0 0 1 6 6c0 4-6 10-6 10S0 10 0 6a6 6 0 0 1 6-6z" fill="var(--green)"/><circle cx="6" cy="6" r="2" fill="#fff"/></svg><div><b>Business Hours</b>Monday to Saturday: 8:00 am to 4:00 pm</div></div>
  </div>
  <div class="abs f-col" style="left:714px">
    <h6>Company</h6>
    <ul class="f-links"><li>Home</li><li>Services</li><li>Testimonials</li><li>About Us</li><li>Contact Us</li></ul>
  </div>
  <div class="abs f-col" style="left:862px;width:240px">
    <h6>Still Have Questions?</h6>
    <p>Contact us using this form. A representative will aswer your questions as soon as possible.</p>
    <span class="btn btn-green">Get a Quote</span>
  </div>
</footer>
<div class="abs foot-line"></div>
<div class="abs go-up">▲ Go Up</div>
<div class="abs copyright">© 2025 Kestrel Services | All Rights Reserved</div>
<div class="abs legal">Privacy Policy &nbsp;|&nbsp; Cookie Policy &nbsp;|&nbsp; Terms Of Services</div>

</body>
</html>
```